Stationery Set for Velmora Company

I need to create full stationery design for my company; Business Cards, Envelops, Letter Heads, Calendar.
In the letter head and Envelops... only contact information and website links.
Our company is a Service Management company with different domains of innovative services including Technology Service Management, Education Services, Outsourcing Management, Events Management.
I need a modern and innovative design specially for the business card. I some transparent designs and I like it, but don't limit your innovation to what I mentioned. Sky is limit for your innovation.

Target Market(s)

Middle East & Africa

Industry/Entity Type

Business Management

Colors
34a7d8
0355a3
85acd3
86cae7
cee9f5
cfdeed
e4daeb
f3f1f8
ecf7fb

Requirements
Must have
• Name, Title, Email, Mobile
Nice to have
• We have multiple locations in USA, KSA, EGY, so I need ideas about how to include all contact details maybe QR / Barcode or something else.
• Please see our locations and contact information: www.brightvelmora.example
Should not have
• Too much text

```html
<!DOCTYPE html>
<html lang="en">
<head>
<meta charset="utf-8">
<title>Velmora Company – Business Card</title>
<link rel="stylesheet" href="https://fonts.googleapis.com/css2?family=Fira+Sans:ital,wght@0,400;0,500;1,500&display=swap">
<style>
  :root {
    --backdrop: #d9dadc;
    --card: #f4f4f6;
    --brand-blue: #3a62ac;
    --ink: #1d1d1f;
    --icon: #3a62ac;
  }
  * { margin: 0; padding: 0; box-sizing: border-box; }
  html, body {
    width: 1105px; height: 1200px; overflow: hidden;
    background: var(--backdrop);
    font-family: "Fira Sans", Arial, sans-serif;
    color: var(--ink);
  }
  .card {
    position: absolute; left: 180px; width: 746px; height: 428px;
    background: var(--card);
  }
  .card--front { top: 118px; }
  .card--back { top: 636px; }
  .card__tab {
    position: absolute; top: 140px; width: 11px; height: 146px;
    background: var(--brand-blue);
  }
  .card__tab--left { left: 0; border-radius: 0 10px 10px 0; }
  .card__tab--right { right: 0; border-radius: 10px 0 0 10px; }

  .brand {
    position: absolute; left: 100px; top: 190px;
    display: flex; align-items: center; gap: 12px;
    font-size: 31px; font-weight: 500; color: var(--brand-blue);
    white-space: nowrap;
  }
  .brand__dot { width: 16px; height: 16px; border-radius: 50%; background: var(--brand-blue); }
  .card--back .brand { left: 88px; }

  .identity { position: absolute; left: 404px; top: 104px; }
  .identity__name { font-size: 31px; font-weight: 500; color: var(--brand-blue); line-height: 1.1; }
  .identity__title { font-size: 19px; margin-top: 8px; }

  .contacts { position: absolute; left: 404px; top: 181px; list-style: none; }
  .contacts li {
    display: flex; align-items: center; gap: 10px;
    font-size: 18px; height: 28px;
  }
  .contacts svg { width: 17px; height: 17px; flex: none; fill: var(--icon); }

  .offices { position: absolute; left: 406px; top: 92px; font-size: 20px; line-height: 28px; }
  .offices__region { color: var(--brand-blue); font-weight: 500; font-style: italic; }
</style>
</head>
<body>

<section class="card card--front">
  <span class="card__tab card__tab--left"></span>
  <span class="card__tab card__tab--right"></span>

  <div class="brand"><span class="brand__dot"></span>Velmora Company</div>

  <div class="identity">
    <h1 class="identity__name">Adam Carter</h1>
    <p class="identity__title">CEO/Founder</p>
  </div>

  <ul class="contacts">
    <li>
      <svg viewBox="0 0 24 24"><path d="M6.6 10.8a15.1 15.1 0 0 0 6.6 6.6l2.2-2.2a1 1 0 0 1 1-.25 11.4 11.4 0 0 0 3.6.57 1 1 0 0 1 1 1V20a1 1 0 0 1-1 1A17 17 0 0 1 3 4a1 1 0 0 1 1-1h3.5a1 1 0 0 1 1 1c0 1.25.2 2.45.57 3.57a1 1 0 0 1-.25 1z"/></svg>
      +1.5550142870 (USA)
    </li>
    <li>
      <svg viewBox="0 0 24 24"><path d="M6.6 10.8a15.1 15.1 0 0 0 6.6 6.6l2.2-2.2a1 1 0 0 1 1-.25 11.4 11.4 0 0 0 3.6.57 1 1 0 0 1 1 1V20a1 1 0 0 1-1 1A17 17 0 0 1 3 4a1 1 0 0 1 1-1h3.5a1 1 0 0 1 1 1c0 1.25.2 2.45.57 3.57a1 1 0 0 1-.25 1z"/></svg>
      +966 90000 31 76 (Saudi)
    </li>
    <li>
      <svg viewBox="0 0 24 24"><path d="M7 1h10a2 2 0 0 1 2 2v18a2 2 0 0 1-2 2H7a2 2 0 0 1-2-2V3a2 2 0 0 1 2-2zm0 3v14h10V4zm5 15.5a1.2 1.2 0 1 0 0 2.4 1.2 1.2 0 0 0 0-2.4z"/></svg>
      +1.5550142870
    </li>
    <li>
      <svg viewBox="0 0 24 24"><path d="M2 5h20v14H2zm2 2v.4l8 5.2 8-5.2V7zm0 2.8V17h16V9.8l-8 5.2z"/></svg>
      info@brightvelmora.example
    </li>
    <li>
      <svg viewBox="0 0 24 24"><path d="M12 2a10 10 0 1 0 0 20 10 10 0 0 0 0-20zm6.9 6h-2.9a15.6 15.6 0 0 0-1.4-3.6A8 8 0 0 1 18.9 8zM12 4c.8 1.2 1.5 2.5 1.9 4h-3.8c.4-1.5 1.1-2.8 1.9-4zM4.3 14a8.2 8.2 0 0 1 0-4h3.4a16 16 0 0 0 0 4zm.8 2h2.9c.3 1.3.8 2.5 1.4 3.6A8 8 0 0 1 5.1 16zM8 8H5.1a8 8 0 0 1 4.3-3.6C8.8 5.5 8.3 6.7 8 8zm4 12c-.8-1.2-1.5-2.5-1.9-4h3.8c-.4 1.5-1.1 2.8-1.9 4zm2.3-6H9.7a14.6 14.6 0 0 1 0-4h4.6a14.6 14.6 0 0 1 0 4zm.3 5.6c.6-1.1 1.1-2.3 1.4-3.6h2.9a8 8 0 0 1-4.3 3.6zm1.7-5.6a16 16 0 0 0 0-4h3.4a8.2 8.2 0 0 1 0 4z"/></svg>
      www.brightvelmora.example
    </li>
  </ul>
</section>

<section class="card card--back">
  <span class="card__tab card__tab--left"></span>
  <span class="card__tab card__tab--right"></span>

  <div class="brand"><span class="brand__dot"></span>Velmora Company</div>

  <address class="offices" style="font-style: normal;">
    <p class="offices__region">USA:</p>
    <p>418 Harbor Crest Lane</p>
    <p>4th Floor Lakeview City</p>
    <p>CA 90210 US</p>
    <p class="offices__region">Saudi Arabia:</p>
    <p>Riyadh, Al Nakheel,</p>
    <p>Fahad Al Qasimi St.</p>
    <p>Noor Business Park</p>
    <p>Block 3A 1st Floor C12, C14</p>
  </address>
</section>

</body>
</html>
```